KTR Design Business Card

I need to develop a business card for my real estate design and investment company. Something clean, classic and professional with a modern vibe.

Industry/Entity Type

Real Estate

Font styles to use
Serif
Sans Serif

```html
<!DOCTYPE html>
<html lang="en">
<head>
<meta charset="utf-8">
<title>KTR Design – Business Card</title>
<link rel="stylesheet" href="https://fonts.googleapis.com/css2?family=Cinzel:wght@400;600&family=Montserrat:wght@300;400&display=swap">
<style>
  :root{
    --backdrop:#e4e4e2;
    --card-dark:#3b3b3b;
    --band-grey:#a9a9a9;
    --panel-white:#fbfbfb;
    --panel-shade:#ececec;
    --ink-light:#f4f4f4;
    --ink-dark:#2e2e2e;
  }
  html,body{margin:0;padding:0;overflow:hidden;}
  body{width:1200px;height:900px;background:var(--backdrop);}
  .sheet{width:1200px;height:900px;position:relative;}
  .card{position:absolute;left:285px;width:630px;height:360px;border-radius:34px;overflow:hidden;
        box-shadow:0 6px 18px rgba(0,0,0,.18);}
  .card--front{top:60px;}
  .card--back{top:480px;}
  .card svg{display:block;}
  .brand{font-family:"Montserrat",sans-serif;font-weight:300;letter-spacing:.06em;}
  .person-name{font-family:"Cinzel",serif;font-weight:600;letter-spacing:.12em;}
  .small-caps{font-family:"Cinzel",serif;font-weight:400;letter-spacing:.1em;}
  .contact{font-family:"Montserrat",sans-serif;font-weight:400;letter-spacing:.14em;}
</style>
</head>
<body>
<main class="sheet">

  <section class="card card--front" aria-label="Business card front">
    <svg width="630" height="360" viewBox="0 0 630 360">
      <defs>
        <linearGradient id="panelFade" x1="0" y1="0" x2="0" y2="1">
          <stop offset="0" stop-color="var(--panel-white)"/>
          <stop offset="1" stop-color="var(--panel-shade)"/>
        </linearGradient>
      </defs>
      <rect class="card-base" width="630" height="360" fill="var(--card-dark)"/>
      <path class="accent-band" d="M0,0 H630 V212 C470,212 230,166 0,148 Z" fill="var(--band-grey)"/>
      <path class="top-panel" d="M0,0 H630 V196 C470,196 230,150 0,132 Z" fill="url(#panelFade)"/>

      <text class="brand" x="315" y="112" text-anchor="middle" font-size="40" fill="var(--ink-dark)">KTR Design</text>

      <g class="identity" text-anchor="end" fill="var(--ink-light)">
        <text class="person-name" x="292" y="238" font-size="15">Daniel Reyes</text>
        <text class="small-caps" x="292" y="256" font-size="11">Owner / C.E.O</text>
        <text class="small-caps" x="292" y="284" font-size="11">Suite # 118, Elm Bldg,</text>
        <text class="small-caps" x="292" y="302" font-size="11">NY 10027</text>
      </g>

      <line class="divider" x1="306" y1="224" x2="306" y2="342" stroke="var(--ink-light)" stroke-width="1"/>

      <g class="contact-block" transform="translate(0,24)">
        <g class="contact-icons" fill="var(--ink-light)">
          <circle cx="324" cy="222" r="6"/>
          <circle cx="324" cy="241" r="6"/>
          <circle cx="324" cy="260" r="6"/>
          <circle cx="324" cy="279" r="6"/>
          <circle cx="324" cy="298" r="6"/>
        </g>
        <g class="contact-glyphs" fill="none" stroke="var(--card-dark)" stroke-width="1.2" stroke-linecap="round">
          <path d="M321.5,219 q0,5 5,6"/>
          <rect x="322" y="237.5" width="4" height="7" rx="0.8"/>
          <rect x="321" y="258" width="6" height="4"/><path d="M322.5,258 v-2 h3 v2"/>
          <rect x="320.5" y="276.5" width="7" height="5"/><path d="M320.5,276.5 l3.5,3 l3.5,-3"/>
          <circle cx="324" cy="298" r="3.5"/><path d="M320.5,298 h7 M324,294.5 v7"/>
        </g>
        <g class="contact" fill="var(--ink-light)" font-size="12.5">
          <text x="336" y="226">555-214-0187</text>
          <text x="336" y="245">555-386-4420</text>
          <text x="336" y="264">555-902-7753</text>
          <text x="336" y="283">hello@ktrdesign.com</text>
          <text x="336" y="302">www.ktrdesign.com</text>
        </g>
      </g>
    </svg>
  </section>

  <section class="card card--back" aria-label="Business card back">
    <svg width="630" height="360" viewBox="0 0 630 360">
      <rect class="card-base" width="630" height="360" fill="var(--card-dark)"/>
      <path class="accent-band" d="M0,150 C200,170 430,230 630,300 V360 H0 Z" fill="var(--band-grey)"/>
      <path class="lower-panel" d="M0,205 C200,222 430,282 630,350 V360 H0 Z" fill="var(--card-dark)"/>
      <text class="brand" x="400" y="120" text-anchor="middle" font-size="40" fill="var(--ink-light)">KTR Design</text>
      <text class="contact" x="70" y="196" font-size="14" fill="var(--ink-light)" transform="rotate(6 70 196)">www.ktrdesign-studio.com</text>
    </svg>
  </section>

</main>
</body>
</html>
```